W. Darrow Billboard

2 miles ahead on right
Voted number 1 ... again!
California cuisine
Located in Historic Marbury Hill Inn
Picture of a couple dining
www.torvellis.com 555.317.2968

Target Market(s)

travelers

Industry/Entity Type

hospitality

Font styles to use
Serif

Colors
59FF00
82FF00
B8FF75
E3FFCB
F4FFEA
EE7325
F08F49
F5BC92
FAE3D3
FDF4ED

Requirements
Should not have
• bright colors

```html
<!DOCTYPE html>
<html lang="en">
<head>
<meta charset="utf-8">
<title>Torvelli's Billboard</title>
<link href="https://fonts.googleapis.com/css2?family=Archivo:ital,wdth,wght@1,125,900&family=Barlow+Semi+Condensed:wght@600;700&family=Barlow+Condensed:wght@600&family=Poppins:wght@500&display=swap" rel="stylesheet">
<style>
  :root {
    --page: #dedede;
    --paper: #ffffff;
    --lime: #bfd833;
    --orange: #ec4a24;
    --ink: #111111;
    --night: #0c0a09;
  }
  * { margin: 0; padding: 0; box-sizing: border-box; }
  html, body { width: 1192px; height: 1200px; overflow: hidden; background: var(--page); }
  .billboard {
    position: absolute; left: 36px; top: 437px; width: 1120px; height: 325px;
    background: var(--paper); overflow: hidden;
    box-shadow: 0 12px 22px rgba(0,0,0,.28);
  }
  .panel { position: absolute; inset: 0; }
  .panel--lime { background: var(--lime); clip-path: polygon(485px 0, 885px 0, 828px 242px, 427px 242px); }
  .panel--orange { background: var(--orange); clip-path: polygon(428px 242px, 826px 242px, 796px 325px, 399px 325px); }
  .panel--photo {
    clip-path: polygon(885px 0, 1120px 0, 1120px 325px, 808px 325px);
    background:
      linear-gradient(180deg, rgba(12,10,9,0) 55%, var(--night) 80%),
      radial-gradient(ellipse at 65% 45%, #a8764a 0%, #6b4528 40%, #2a1a12 80%);
  }
  .accents { position: absolute; inset: 0; }
  .brand {
    position: absolute; left: 20px; width: 400px; top: 92px; text-align: center;
    font-family: "Barlow Semi Condensed", sans-serif; font-weight: 700; color: var(--orange);
  }
  .brand__name { font-size: 88px; line-height: .95; }
  .brand__sub { font-size: 27px; letter-spacing: 2px; text-transform: uppercase; margin-top: 6px; }
  .web {
    position: absolute; left: 65px; top: 268px; width: 290px; text-align: center;
    font-family: "Poppins", sans-serif; font-weight: 500; font-size: 31px; color: var(--ink);
  }
  .headline { font-family: "Archivo", sans-serif; font-style: italic; font-stretch: 125%; font-weight: 900; color: var(--ink); position: absolute; line-height: 1; }
  .headline--voted { left: 506px; top: 26px; font-size: 76px; letter-spacing: -1px; }
  .headline--rank { left: 478px; top: 92px; font-size: 104px; letter-spacing: -2px; }
  .headline--again { left: 540px; top: 192px; font-size: 36px; }
  .tagline {
    position: absolute; left: 410px; width: 410px; text-align: center; color: #fff;
    font-family: "Barlow Semi Condensed", sans-serif; font-weight: 600;
  }
  .tagline--cuisine { top: 250px; font-size: 31px; }
  .tagline--place { top: 285px; font-size: 22px; }
  .phone {
    position: absolute; left: 838px; top: 258px; width: 262px; text-align: center;
    font-family: "Barlow Condensed", sans-serif; font-weight: 600; font-size: 54px; color: #fff; line-height: 1;
  }
</style>
</head>
<body>
  <section class="billboard">
    <div class="panel panel--lime"></div>
    <div class="panel panel--orange"></div>
    <div class="panel panel--photo" role="img" aria-label="Photo of a couple sharing red wine at a candlelit dinner"></div>
    <svg class="accents" width="1120" height="325" viewBox="0 0 1120 325">
      <line x1="484" y1="3" x2="463" y2="68" stroke="var(--orange)" stroke-width="5"/>
      <circle cx="459" cy="79" r="4" fill="var(--orange)"/>
      <line x1="842" y1="203" x2="798" y2="325" stroke="var(--lime)" stroke-width="5"/>
      <circle cx="845" cy="193" r="4" fill="var(--lime)"/>
    </svg>
    <div class="brand">
      <div class="brand__name">Torvelli's</div>
      <div class="brand__sub">Southwest Bar &amp; Grill</div>
    </div>
    <div class="web">www.torvellis.com</div>
    <div class="headline headline--voted">VOTED</div>
    <div class="headline headline--rank">NO.1</div>
    <div class="headline headline--again">... AGAIN!</div>
    <div class="tagline tagline--cuisine">CALIFORNIA CUISINE</div>
    <div class="tagline tagline--place">Located in Historic Marbury Hill Inn</div>
    <div class="phone">555.317.2968</div>
  </section>
</body>
</html>
```